Business Card for Vorla Parts Wholesale supplier

Hi There! I need a new business card for our company. We are specialized in selling Vorla parts, mostly we sell new LCD screens for Zelnar and Drelks. I would like to see that back in the design.

You can find the colors and logo's on our website: www.hartuvo.nl

Industry/Entity Type

Business

Contact Information for Business Card

My Details:
Tobias Lindqvist

Phone: 0031687203316
E-mail: Tobias@hartuvo.nl

Slogan: "Because Quality Matters"

Font styles to use
Sans Serif

Colors

Designer to choose colors to be used in the design.

Requirements
Must have
• A Black backside with the Hartuvo logo on it. The front side should be clean with only my contact details.
• But I'm also open for something really different or awesome!
Nice to have
• Remember that we are in the parts & repairing industry, So i'll be handing those business cards mainly to repair companies. Maybe you can do something with that thought :)

```html
<!DOCTYPE html>
<html lang="en">
<head>
<meta charset="utf-8">
<title>Hartuvo Business Card</title>
<link rel="stylesheet" href="https://fonts.googleapis.com/css2?family=Roboto:wght@400;500;700&display=swap">
<style>
  :root {
    --stage: #e6e6e6;
    --ink-dark: #141416;
    --ink-panel: #1d1d1f;
    --brand-orange: #e8731f;
    --paper-white: #f5f5f5;
    --text-light: #f2f2f2;
    --text-dark: #1a1a1a;
  }
  * { margin: 0; padding: 0; box-sizing: border-box; }
  html, body {
    width: 1200px; height: 576px; overflow: hidden;
    background: var(--stage);
    font-family: "Roboto", Arial, sans-serif;
  }
  .canvas { position: relative; width: 1200px; height: 576px; }
  .card {
    position: absolute; top: 138px;
    width: 484px; height: 294px;
    border-radius: 16px; overflow: hidden;
    background: var(--ink-dark);
    box-shadow: 0 4px 10px rgba(0,0,0,0.25);
  }
  .card--back { left: 82px; }
  .card--front { left: 602px; }

  /* back side */
  .back-photo {
    position: absolute; inset: 0;
    background:
      radial-gradient(ellipse 55% 45% at 70% 25%, rgba(90,90,95,0.35), transparent 70%),
      linear-gradient(160deg, #1a1a1c 0%, #2a2a2c 45%, #1c1c1d 70%, #232324 100%);
  }
  .wordmark {
    position: absolute; display: flex; align-items: center; gap: 12px;
    font-weight: 700; letter-spacing: 0.5px; line-height: 1;
  }
  .wordmark__mark { width: 26px; height: 26px; background: var(--brand-orange); border-radius: 5px; }
  .card--back .wordmark {
    left: 104px; top: 126px; font-size: 44px; color: var(--text-light);
  }

  /* front side */
  .front-shape { position: absolute; inset: 0; }
  .holder { position: absolute; left: 29px; top: 42px; }
  .holder__name { font-size: 18px; font-weight: 500; color: var(--brand-orange); }
  .holder__role { font-size: 11.5px; color: var(--text-light); margin-top: 4px; }
  .contacts { position: absolute; left: 29px; top: 168px; list-style: none; }
  .contacts li {
    display: flex; align-items: center; gap: 10px;
    height: 17px; font-size: 12px; color: var(--text-light);
  }
  .contacts svg { width: 12px; height: 12px; fill: var(--brand-orange); }
  .slogan {
    position: absolute; left: 29px; top: 249px;
    font-size: 12.5px; color: var(--text-light);
  }
  .card--front .wordmark {
    left: 296px; top: 148px; font-size: 38px; color: var(--text-dark); gap: 10px;
  }
  .card--front .wordmark__mark { width: 20px; height: 20px; }
</style>
</head>
<body>
<main class="canvas">
  <section class="card card--back">
    <div class="back-photo" role="img" aria-label="Dark close-up photo of a smartphone with a cracked screen"></div>
    <div class="wordmark"><span class="wordmark__mark"></span><span>hartuvo</span></div>
  </section>

  <section class="card card--front">
    <svg class="front-shape" viewBox="0 0 484 294" width="484" height="294" aria-hidden="true">
      <rect width="484" height="294" fill="var(--ink-dark)"/>
      <rect x="0" y="240" width="300" height="34" fill="var(--brand-orange)"/>
      <path d="M281 0 Q200 105 237 206 Q215 100 291 0 Z" fill="var(--brand-orange)"/>
      <path d="M295 0 Q201 147 295 294 L484 294 L484 0 Z" fill="var(--paper-white)"/>
    </svg>

    <div class="holder">
      <p class="holder__name">Tobias Lindqvist</p>
      <p class="holder__role">Managing Director</p>
    </div>

    <ul class="contacts">
      <li>
        <svg viewBox="0 0 24 24"><path d="M4 9c0-3 3-5 8-5s8 2 8 5v2h-4V9H8v2H4zM6 12h12l2 8H4z"/></svg>
        <span>0031687203316</span>
      </li>
      <li>
        <svg viewBox="0 0 24 24"><path d="M12 2a10 10 0 1 0 0 20 10 10 0 0 0 0-20zm0 2c1 0 2.5 2.5 2.8 7H9.2C9.5 6.5 11 4 12 4zm-3.7 1A13 13 0 0 0 7.2 11H4.1a8 8 0 0 1 4.2-6zm7.4 0a8 8 0 0 1 4.2 6h-3.1a13 13 0 0 0-1.1-6zM4.1 13h3.1a13 13 0 0 0 1.1 6 8 8 0 0 1-4.2-6zm5.1 0h5.6c-.3 4.5-1.8 7-2.8 7s-2.5-2.5-2.8-7zm7.6 0h3.1a8 8 0 0 1-4.2 6 13 13 0 0 0 1.1-6z"/></svg>
        <span>Tobias@hartuvo.nl</span>
      </li>
      <li>
        <svg viewBox="0 0 24 24"><path d="M2 5h20v14H2zm2 2v.5l8 5 8-5V7z"/></svg>
        <span>www.hartuvo.nl</span>
      </li>
    </ul>

    <p class="slogan">Because Quality Matters</p>

    <div class="wordmark"><span class="wordmark__mark"></span><span>hartuvo</span></div>
  </section>
</main>
</body>
</html>
```